Personal Motivational Quote Poster Design

I would like to create a poster with some of my favorite quotes to hang in my office. I did similar projects in 2012 and 2014. I've uploaded the winning designs so you can get a better idea of what I'm looking for. I will provide feedback on your design within 24 hours of receiving it.

The poster must contain the following quotes:

“What the pupil must learn, if he learns anything at all, is that the world will do most of the work for you, provided you cooperate with it by identifying how it really works and aligning with those realities. If we do not let the world teach us, it teaches us a lesson.” - Harold Quenby

“I tackle every big new problem by asking two questions: Who has dealt with this problem well? And what can we learn from them?” - Walt Prisco

“If we can really understand the problem, the answer will come out of it, because the answer is not separate from the problem.” - Ravindra Selvapathi

“Success is nothing more than a few simple disciplines, practiced every day; while failure is simply a few errors in judgment, repeated every day. It is the accumulative weight of our disciplines and our judgments that leads us to either fortune or failure.” - Ned Falco

“Inaction breeds doubt and fear. Action breeds confidence and courage.” - Rufus Pembrook

“What’s the one thing you can do, such that by doing it, everything else will be easier or unnecessary?” - Lyle Dorsey

Requirements
Must have
• The poster will be 24" high x 36" long and printed on canvas, so the image you create needs to have a resolution of at least 2700 x 3900.
Nice to have
• I don't have an exact vision for how the poster should look, so I am totally open to you using your creativity to develop, arrange and present the content as you'd like.

That said, I would like an image (photo or posterized image) of the person being quoted along with each quote. I do not have specific images that I would like you to use, so you will need to find the images on your own.

The images don't need to be perfect... I am more interested in the poster relating the essence of the quotes and the people being quoted than I am in perfect photographic images of the people being quoted.

```html
<!DOCTYPE html>
<html lang="en">
<head>
<meta charset="utf-8">
<title>Quote Poster</title>
<link rel="stylesheet" href="https://fonts.googleapis.com/css2?family=Delius&family=Indie+Flower&display=swap">
<style>
  :root {
    --wall: #e9e9e8;
    --wall-shade: #dcdcda;
    --amber: #fbab5a;
    --amber-tone: #c98a55;
    --tangerine: #f26a23;
    --tangerine-tone: #c9683f;
    --raspberry: #cc2a5e;
    --raspberry-tone: #e0557f;
    --teal: #79cdc7;
    --teal-tone: #5fa7a1;
    --indigo: #5e5aa8;
    --indigo-tone: #4a4a86;
    --sky: #7ba7da;
    --sky-tone: #5776a3;
    --ink: #ffffff;
    --frame: rgba(255, 255, 255, 0.85);
  }
  * { box-sizing: border-box; margin: 0; padding: 0; }
  html, body { width: 1200px; height: 800px; overflow: hidden; }
  body {
    background: radial-gradient(ellipse at 50% 40%, #f2f2f1 0%, var(--wall) 60%, var(--wall-shade) 100%);
    font-family: "Delius", "Comic Sans MS", sans-serif;
    color: var(--ink);
    position: relative;
  }
  .quote-card {
    position: absolute;
    overflow: visible;
  }
  .card-fill {
    position: absolute;
    inset: 0;
  }
  .card-frame {
    position: absolute;
    border: 2px solid var(--frame);
    pointer-events: none;
  }
  .portrait {
    position: absolute;
    opacity: 0.75;
  }
  .quote {
    position: absolute;
    font-size: 20px;
    line-height: 1.3;
    z-index: 2;
  }
  .quote .big { font-size: 31px; }
  .quote .mid { font-size: 25px; }
  .quote .small { font-size: 17px; }
  .author {
    position: absolute;
    font-family: "Indie Flower", cursive;
    font-size: 20px;
    z-index: 2;
    letter-spacing: 0.5px;
  }

  /* Harold Quenby */
  .card-quenby { left: 22px; top: 51px; width: 585px; height: 250px; transform: rotate(0.15deg); }
  .card-quenby .card-fill { background: var(--amber); }
  .card-quenby .card-frame { left: 8px; top: -13px; width: 575px; height: 248px; transform: rotate(0.4deg); }
  .card-quenby .portrait { left: 420px; top: 104px; width: 166px; height: 146px;
    background: radial-gradient(ellipse at 55% 30%, #e8b48a 0%, var(--amber-tone) 55%, #8f6a4f 100%); }
  .card-quenby .quote { left: 26px; top: 24px; width: 552px; text-align: justify; line-height: 1.32; font-size: 20px; }
  .card-quenby .quote .lead { display: block; text-indent: 28px; }
  .card-quenby .quote .big { display: block; line-height: 1.15; margin-top: 4px; text-indent: 12px; font-size: 30px; }
  .card-quenby .author { left: 30px; top: 205px; }

  /* Walt Prisco */
  .card-prisco { left: 32px; top: 312px; width: 580px; height: 216px; transform: rotate(-0.5deg); }
  .card-prisco .card-fill { background: var(--tangerine); }
  .card-prisco .card-frame { left: 2px; top: 9px; width: 576px; height: 190px; transform: rotate(0.5deg); }
  .card-prisco .portrait { left: 84px; top: 72px; width: 180px; height: 138px;
    background: radial-gradient(ellipse at 55% 35%, #e59b77 0%, var(--tangerine-tone) 55%, #8a4a30 100%); }
  .card-prisco .quote { left: 20px; top: 22px; width: 545px; line-height: 40px; }
  .card-prisco .author { left: 26px; top: 160px; }

  /* Ravindra Selvapathi */
  .card-selvapathi { left: 22px; top: 536px; width: 580px; height: 214px; transform: rotate(-0.4deg); }
  .card-selvapathi .card-fill { background: var(--raspberry); }
  .card-selvapathi .card-frame { left: 8px; top: -3px; width: 570px; height: 192px; transform: rotate(0.4deg); }
  .card-selvapathi .portrait { left: 428px; top: 60px; width: 146px; height: 154px;
    background: radial-gradient(ellipse at 50% 35%, #f08aa8 0%, var(--raspberry-tone) 55%, #a52a55 100%); }
  .card-selvapathi .quote { left: 30px; top: 8px; width: 540px; line-height: 40px; }
  .card-selvapathi .author { left: 36px; top: 144px; }

  /* Rufus Pembrook */
  .card-pembrook { left: 610px; top: 22px; width: 568px; height: 232px; transform: rotate(-0.9deg); }
  .card-pembrook .card-fill { background: var(--teal); }
  .card-pembrook .card-frame { left: 10px; top: 12px; width: 548px; height: 200px; transform: rotate(0.6deg); }
  .card-pembrook .portrait { left: 26px; top: 76px; width: 150px; height: 136px;
    background: radial-gradient(ellipse at 50% 35%, #9fd3ce 0%, var(--teal-tone) 55%, #3f7f7a 100%); }
  .card-pembrook .quote { right: 40px; top: 58px; width: 500px; text-align: right; line-height: 42px; }
  .card-pembrook .author { right: 40px; top: 186px; }

  /* Ned Falco */
  .card-falco { left: 607px; top: 260px; width: 570px; height: 254px; transform: rotate(0.4deg); }
  .card-falco .card-fill { background: var(--indigo); }
  .card-falco .card-frame { left: 10px; top: -3px; width: 552px; height: 252px; }
  .card-falco .portrait { left: 300px; top: 112px; width: 256px; height: 140px;
    background: radial-gradient(ellipse at 65% 35%, #8a86c4 0%, var(--indigo-tone) 60%, #353566 100%); }
  .card-falco .quote { left: 36px; top: 10px; width: 504px; text-align: justify; text-align-last: right; line-height: 33px; font-size: 19px; }
  .card-falco .author { right: 20px; top: 222px; font-size: 19px; }

  /* Lyle Dorsey */
  .card-dorsey { left: 598px; top: 531px; width: 580px; height: 226px; transform: rotate(-0.5deg); }
  .card-dorsey .card-fill { background: var(--sky); }
  .card-dorsey .card-frame { left: 12px; top: 4px; width: 566px; height: 218px; transform: rotate(0.3deg); }
  .card-dorsey .portrait { left: 50px; top: 80px; width: 130px; height: 144px;
    background: radial-gradient(ellipse at 50% 30%, #a5bfe0 0%, var(--sky-tone) 55%, #3a4f73 100%); }
  .card-dorsey .quote { right: 32px; top: 36px; width: 510px; text-align: right; line-height: 30px; }
  .card-dorsey .quote .big { line-height: 40px; word-spacing: 6px; }
  .card-dorsey .author { right: 32px; top: 162px; }
</style>
</head>
<body>
<main class="poster">

  <section class="quote-card card-quenby">
    <div class="card-fill"></div>
    <div class="portrait" role="img" aria-label="Tinted portrait photo of Harold Quenby"></div>
    <div class="card-frame"></div>
    <p class="quote"><span class="lead">What the pupil must learn, if he learns anything at all, is that the world will do most of the work for you, provided you cooperate with it by identifying how it really works and aligning with those realities.</span><span class="big">If we do not let the world teach us, it teaches us a lesson.”</span></p>
    <p class="author">- Harold Quenby</p>
  </section>

  <section class="quote-card card-prisco">
    <div class="card-fill"></div>
    <div class="portrait" role="img" aria-label="Tinted portrait photo of Walt Prisco"></div>
    <div class="card-frame"></div>
    <p class="quote">“I tackle every big new problem by asking two<br>questions: <span class="big">Who</span> has dealt with this problem well?<br>And <span class="big">what</span> can we learn from them?”</p>
    <p class="author">- Walt Prisco</p>
  </section>

  <section class="quote-card card-selvapathi">
    <div class="card-fill"></div>
    <div class="portrait" role="img" aria-label="Tinted portrait photo of Ravindra Selvapathi"></div>
    <div class="card-frame"></div>
    <p class="quote">“If we can really understand the problem, the answer<br>will come out of it, because <span class="big">the answer is not</span><br><span class="big">separate from the problem.”</span></p>
    <p class="author">- Ravindra Selvapathi</p>
  </section>

  <section class="quote-card card-pembrook">
    <div class="card-fill"></div>
    <div class="portrait" role="img" aria-label="Tinted portrait photo of Rufus Pembrook"></div>
    <div class="card-frame"></div>
    <p class="quote"><span class="big">Inaction</span> breeds <span class="mid">doubt and fear.</span><br><span class="big">Action</span> breeds <span class="mid">confidence and courage.”</span></p>
    <p class="author">- Rufus Pembrook</p>
  </section>

  <section class="quote-card card-falco">
    <div class="card-fill"></div>
    <div class="portrait" role="img" aria-label="Tinted photo of Ned Falco speaking"></div>
    <div class="card-frame"></div>
    <p class="quote">“<span class="big">Success</span> is nothing more than a few simple disciplines, practiced every day; while <span class="big">failure</span> is simply a few errors in judgment, repeated every day. It is the accumulative weight of <span class="mid">our disciplines and our judgments</span> that <span class="mid">leads us to either fortune or failure.”</span></p>
    <p class="author">- Ned Falco</p>
  </section>

  <section class="quote-card card-dorsey">
    <div class="card-fill"></div>
    <div class="portrait" role="img" aria-label="Tinted portrait photo of Lyle Dorsey"></div>
    <div class="card-frame"></div>
    <p class="quote">“What’s <span class="big">the one thing you can do,</span><br>such that by doing it, everything else will be easier<br>or unnecessary?”</p>
    <p class="author">- Lyle Dorsey</p>
  </section>

</main>
</body>
</html>
```